Salon and Spa Distributor Business Card

Need a business card. We are are distributor in the salon and spa industry. We identify with natural beauty. Need a card with:
Company Name: Petal Quarry"
Title: "President & CEO"
Address
Company Phone number
email
website
Tag Line:" The Professional Salon Source"

Industry/Entity Type

Business

Contact Information for Business Card

Name: Dov Strommen
Title: "President & CEO"
Address: 31 Harlow Ln, Bexmoor, NJ 07813
Company Phone number: 800-463-5918
email: dovstrommen@petalquarry.example
website: www.petalquarry.example

Requirements
Should not have
• No black backgrounds

```html
<!DOCTYPE html>
<html lang="en">
<head>
<meta charset="utf-8">
<title>Petal Quarry – Business Card</title>
<link rel="stylesheet" href="https://fonts.googleapis.com/css2?family=Questrial&display=swap">
<style>
  :root {
    --green-light: #64bc46;
    --green-mid: #3a9a3e;
    --green-deep: #0e6c37;
    --green-soft: #a9d89a;
    --white: #ffffff;
    --canvas: #e4e7e3;
    --card-radius: 22px;
  }
  * { box-sizing: border-box; margin: 0; padding: 0; }
  html, body {
    width: 1200px; height: 880px; overflow: hidden;
    background: var(--canvas);
    font-family: "Questrial", "Century Gothic", sans-serif;
    color: var(--white);
  }
  .canvas { position: relative; width: 1200px; height: 880px; }
  .card {
    position: absolute;
    width: 620px; height: 354px;
    border-radius: var(--card-radius);
    overflow: hidden;
    box-shadow: 0 14px 30px rgba(0,0,0,.22);
    background: linear-gradient(160deg, var(--green-light) 0%, var(--green-mid) 50%, var(--green-deep) 100%);
  }
  .card--front { left: 80px; top: 60px; }
  .card--back { left: 500px; top: 466px; }

  .brand-lockup {
    position: absolute;
    display: flex; align-items: center; gap: 18px;
  }
  .card--front .brand-lockup { left: 130px; top: 118px; }
  .brand-mark {
    width: 140px; height: 118px; border-radius: 12px;
    background: linear-gradient(135deg, rgba(255,255,255,.85), rgba(255,255,255,.55));
  }
  .brand-name { font-size: 44px; letter-spacing: .5px; line-height: 1; font-weight: 400; }
  .brand-tagline { font-size: 15.5px; letter-spacing: 1px; margin-top: 4px; }

  .back-panel {
    position: absolute; right: 0; top: 0;
    width: 250px; height: 354px;
    background: var(--white);
    border-top-left-radius: 120px 200px;
  }
  .back-illustration {
    position: absolute; right: 18px; top: 18px;
    width: 250px; height: 318px;
    border-radius: 90px 30px 30px 60px;
    background: linear-gradient(180deg, var(--green-soft) 0%, var(--green-light) 55%, var(--green-mid) 100%);
  }

  .back-info { position: absolute; left: 40px; top: 42px; }
  .back-info .brand-name { font-size: 40px; }
  .back-info .brand-tagline { font-size: 14px; }

  .person { margin-top: 40px; }
  .person-name { font-size: 22px; letter-spacing: .5px; }
  .person-title { font-size: 15px; margin-top: 2px; }

  .address { margin-top: 30px; font-size: 15px; line-height: 1.35; }

  .contact-list { list-style: none; margin-top: 10px; font-size: 15px; }
  .contact-list li { display: flex; align-items: center; gap: 9px; line-height: 1.55; }
  .contact-icon {
    width: 17px; height: 17px; border-radius: 3px; background: var(--white);
    display: inline-flex; align-items: center; justify-content: center;
  }
  .contact-icon svg { display: block; }
</style>
</head>
<body>
<main class="canvas">

  <section class="card card--front" aria-label="Business card front">
    <div class="brand-lockup">
      <div class="brand-mark" role="img" aria-label="Brand mark: leafy hair silhouette in white"></div>
      <div class="brand-text">
        <div class="brand-name">Petal Quarry</div>
        <div class="brand-tagline">The Professional Salon Source</div>
      </div>
    </div>
  </section>

  <section class="card card--back" aria-label="Business card back">
    <div class="back-panel"></div>
    <div class="back-illustration" role="img" aria-label="Illustration: woman's profile with flowing green hair and leaves"></div>

    <div class="back-info">
      <div class="brand-name">Petal Quarry</div>
      <div class="brand-tagline">The Professional Salon Source</div>

      <div class="person">
        <div class="person-name">Dov Strommen</div>
        <div class="person-title">President &amp; CEO</div>
      </div>

      <div class="address">31 Harlow Ln,<br>Bexmoor, NJ 07813</div>

      <ul class="contact-list">
        <li>
          <span class="contact-icon">
            <svg width="11" height="11" viewBox="0 0 12 12"><path d="M2.5 1 L4.5 1 L5.3 3.5 L4 4.5 C4.7 6 6 7.3 7.5 8 L8.5 6.7 L11 7.5 V9.5 C11 10.3 10.3 11 9.5 11 C5 11 1 7 1 2.5 C1 1.7 1.7 1 2.5 1 Z" fill="#2f8f3d"/></svg>
          </span>800-463-5918
        </li>
        <li>
          <span class="contact-icon">
            <svg width="12" height="9" viewBox="0 0 12 9"><rect x=".5" y=".5" width="11" height="8" fill="none" stroke="#2f8f3d"/><path d="M.5 .5 L6 5 L11.5 .5" fill="none" stroke="#2f8f3d"/></svg>
          </span>dovstrommen@petalquarry.example
        </li>
        <li>
          <span class="contact-icon">
            <svg width="12" height="12" viewBox="0 0 12 12"><circle cx="6" cy="6" r="5" fill="none" stroke="#2f8f3d"/><ellipse cx="6" cy="6" rx="2.2" ry="5" fill="none" stroke="#2f8f3d"/><path d="M1 6 H11" stroke="#2f8f3d"/></svg>
          </span>www.petalquarry.example
        </li>
      </ul>
    </div>
  </section>

</main>
</body>
</html>
```